2 x Digitize Logo | 2 x Business Cards | 2 x Fridge Magnets

We require 6 deliverables:
1. Residential logo redrawn (same just high quality for large print format).
2. Corporate logo redrawn (minor changes to wording and high quality for large print format).
3. New business card design for Furniture Removals (residential)
4. New business card design for Corporate Relocations (business)
5. New Fridge magnet for Furniture removals (residential)
6. New fridge magnet for Corporate Relocations (business)
1. Residential Logo
a. We require the logo to be translated into a high quality digital image with no modifications.
(see attached resilogo.jpg)
2. Residential Logo
a. We require the logo to be edited (add the word corporate relocations) be translated into a high quality digital image.
(see attached corplogo.jpg)
3. Using the resilogo please make a new business card for our business.
a. Please see the web site https://www.larkbendcarters.com.au for colours and inspiration.
b. The residential business card needs the following information:
i. Business Name (using the residential logo).
ii. Free Call: 1800 LB Cart (the L, B and Cart much be the same colour as the logo).
iii. Website: www.LarkbendCarters.com.au
iv. Address: 4/17 Ormsdale Court, VIC 3264
v. Email: cart@LarkbendCarters.com.au
vi. backof Card:
Review our service
www.PennantOrbit.com.au
Services: Local, Country, Interstate | Furniture Removals | Piano, Billiard Tables & Antiques
4. Using the corplogo please make a new business card for our business.
b. The corporate business card needs the following information:
i. Business Name (using the corporate logo).
v. Email: corporate@LarkbendCarters.com.au
vi. Back of Card:
Review our service
www.PennantOrbit.com.au
Services: Corporate relocations | Office equipment moves | Packing Service | Packing Materials
5. Using the resilogo please make a new fridge magent for our business.
b. The residential fidge magnet needs the following information:
iv. Services: Local, Country, Interstate | Furniture Removals | Piano, Billiard Tables & Antiques
6. Using the corplogo please make a new fridge magent for our business.
b. The corporate fidge magnet needs the following information:
iv. Services: Local, Country, Interstate | Corporate relocations
Target Market(s)
Residential Furniture Removals and Corporate Office relocations
Industry/Entity Type
Business
Contact Information for Business Card
Please see full brief for six items required
Requirements
Must have
- Clean simple, easy to read
Nice to have
- fresh, stand out, eye catching
Should not have
- plain, standard, boring, general

```html
<!DOCTYPE html>
<html lang="en">
<head>
<meta charset="utf-8">
<title>Larkbend Carters – Corporate Business Card</title>
<link rel="stylesheet" href="https://fonts.googleapis.com/css2?family=Source+Sans+3:wght@400;600&display=swap">
<style>
  :root {
    --stage: #7f7f7f;
    --card-light: #f2f2f2;
    --card-dark: #141414;
    --brand-red: #b5120f;
    --brand-green: #0e7a3c;
    --ink: #262626;
    --paper-text: #f4f4f4;
  }
  * { margin: 0; padding: 0; box-sizing: border-box; }
  html, body { width: 1200px; height: 900px; overflow: hidden; }
  body {
    background: var(--stage);
    font-family: "Source Sans 3", "Myriad Pro", Arial, sans-serif;
    position: relative;
  }
  .card {
    position: absolute;
    top: 170px;
    width: 347px;
    height: 561px;
    text-align: center;
  }
  .card--front { left: 259px; background: var(--card-light); color: var(--ink); }
  .card--back { left: 631px; background: var(--card-dark); color: var(--paper-text); }

  .brand {
    position: absolute;
    left: 0; right: 0;
    top: 148px;
  }
  .card--back .brand { top: 134px; }
  .brand__name {
    font-size: 21px;
    font-weight: 600;
    letter-spacing: 0.5px;
    color: var(--brand-red);
    line-height: 24px;
  }
  .brand__tagline {
    font-size: 17px;
    font-weight: 400;
    color: var(--brand-green);
    line-height: 22px;
  }

  .contact {
    position: absolute;
    left: 0; right: 0;
    top: 334px;
  }
  .contact__icons { display: flex; justify-content: center; gap: 5px; height: 20px; }
  .contact__icons svg { width: 16px; height: 16px; fill: var(--brand-green); }
  .contact__lines { margin-top: 10px; font-size: 19.5px; line-height: 24.5px; }
  .accent { color: var(--brand-red); }
  .address { position: absolute; left: 0; right: 0; top: 458px; font-size: 19.5px; }
  .address svg { width: 14px; height: 20px; fill: var(--brand-green); display: block; margin: 0 auto 9px; }

  .review { position: absolute; left: 0; right: 0; top: 281px; }
  .review__label { font-size: 16px; line-height: 20px; }
  .review__link { font-size: 20px; line-height: 30px; }

  .services { position: absolute; left: 0; right: 0; top: 398px; }
  .services__title {
    display: flex; align-items: center; justify-content: center; gap: 5px;
    font-size: 16px;
  }
  .services__title::before, .services__title::after {
    content: ""; width: 45px; height: 1px; background: var(--paper-text);
  }
  .services__list { list-style: none; margin-top: 10px; font-size: 16px; line-height: 20.3px; text-transform: uppercase; }
</style>
</head>
<body>
  <section class="card card--front" aria-label="Card front">
    <div class="brand">
      <div class="brand__name">LARKBEND CARTERS</div>
      <div class="brand__tagline">CORPORATE RELOCATIONS</div>
    </div>

    <div class="contact">
      <div class="contact__icons">
        <svg viewBox="0 0 24 24" aria-hidden="true"><path d="M6.6 10.8a15.2 15.2 0 0 0 6.6 6.6l2.2-2.2c.3-.3.7-.4 1-.2 1.1.4 2.3.6 3.6.6.6 0 1 .4 1 1V20c0 .6-.4 1-1 1A17 17 0 0 1 3 4c0-.6.4-1 1-1h3.5c.6 0 1 .4 1 1 0 1.3.2 2.5.6 3.6.1.3 0 .7-.2 1z"/></svg>
        <svg viewBox="0 0 24 24" aria-hidden="true"><path d="M2 5h20v14H2z M3.5 6.5l8.5 6.5 8.5-6.5" stroke="#f2f2f2" stroke-width="1.4"/></svg>
        <svg viewBox="0 0 24 24" aria-hidden="true"><circle cx="12" cy="12" r="10"/><path d="M8 6c2 1 1 3 3 4s0 3 2 4-1 4 0 5M15 5c-1 2 2 2 3 4" stroke="#f2f2f2" stroke-width="1.4" fill="none"/></svg>
      </div>
      <div class="contact__lines">
        <div>1800 <span class="accent">LB Cart</span></div>
        <div>cart@LarkbendCarters.com.au</div>
        <div>www.LarkbendCarters.com.au</div>
      </div>
    </div>

    <div class="address">
      <svg viewBox="0 0 14 20" aria-hidden="true"><path d="M7 0a7 7 0 0 0-7 7c0 5 7 13 7 13s7-8 7-13a7 7 0 0 0-7-7zm0 9.5A2.5 2.5 0 1 1 7 4.5a2.5 2.5 0 0 1 0 5z"/></svg>
      4/17 Ormsdale Court, VIC 3264
    </div>
  </section>

  <section class="card card--back" aria-label="Card back">
    <div class="brand">
      <div class="brand__name">LARKBEND CARTERS</div>
      <div class="brand__tagline">CORPORATE RELOCATIONS</div>
    </div>

    <div class="review">
      <div class="review__label">Review our service</div>
      <div class="review__link">www.PennantOrbit.com.au</div>
    </div>

    <div class="services">
      <div class="services__title">SERVICES</div>
      <ul class="services__list">
        <li>Corporate Relocations</li>
        <li>Office Equipment Moves</li>
        <li>Packing Service</li>
        <li>Packing Materials</li>
      </ul>
    </div>
  </section>
</body>
</html>
```